Veltrane Group Business Card Design

The CEO is looking for a new trendy look for his business card.
You can stay with current branding or come up with something new/creative. It can be 3D, including Medical Office buildings. You can use our logo in a variety of colors. Please include name, title, company name, company website, email address, cell number

Target Market(s)

Real Estate Development and Construction

Industry/Entity Type

Health care real estate

Contact Information for Business Card

Rohesh Kamdar, CEO M-604.781.2249 E-roheshkamdar@veltrane.com Address:4180 Lindqvist Ave, Tampa, FL 33482 www.veltrane.com

Font styles to use
Other font styles liked:
• Be creative

Requirements
Must have
• Creative, trendy look
Nice to have
• Please go to our website to get a feel- www. veltrane.com
Should not have
• small fonts

```html
<!DOCTYPE html>
<html lang="en">
<head>
<meta charset="utf-8">
<title>Veltrane Group Business Card</title>
<link rel="stylesheet" href="https://fonts.googleapis.com/css2?family=Montserrat:wght@300;700;800&display=swap">
<style>
  :root {
    --backdrop: #474746;
    --card: #161616;
    --ink: #ffffff;
    --ink-soft: #e6e6e6;
    --gloss: #3b3b3b;
  }
  * { margin: 0; padding: 0; box-sizing: border-box; }
  html, body { width: 1200px; height: 801px; overflow: hidden; }
  body {
    background: var(--backdrop);
    font-family: "Montserrat", sans-serif;
    display: flex;
    align-items: center;
    justify-content: center;
    gap: 40px;
  }
  .card {
    position: relative;
    width: 540px;
    height: 309px;
    background: var(--card);
    border-radius: 18px;
    color: var(--ink);
    box-shadow: 0 10px 30px rgba(0,0,0,.35);
  }
  .brand-name {
    position: absolute;
    left: 34px;
    top: 108px;
    font-weight: 800;
    font-size: 36px;
    line-height: 1;
    letter-spacing: -1px;
    color: var(--ink);
  }
  .divider {
    position: absolute;
    left: 262px;
    top: 48px;
    width: 1.5px;
    height: 212px;
    background: var(--ink);
  }
  .contact {
    position: absolute;
    left: 282px;
    top: 46px;
    font-weight: 300;
    font-size: 14px;
    line-height: 1.5;
    color: var(--ink-soft);
  }
  .contact-name {
    font-weight: 700;
    font-size: 19px;
    letter-spacing: .5px;
    color: var(--ink);
    line-height: 1.2;
  }
  .contact-title { margin-bottom: 8px; }
  .contact-address { margin-bottom: 8px; }
  .contact-line { display: flex; align-items: center; gap: 7px; }
  .contact-line svg { width: 11px; height: 11px; flex: none; fill: var(--ink); }
  .card-back .brand-mark {
    position: absolute;
    left: 50%;
    top: 50%;
    transform: translate(-50%, -50%);
    font-weight: 800;
    font-size: 78px;
    line-height: .95;
    letter-spacing: -3px;
    color: var(--gloss);
    white-space: nowrap;
  }
</style>
</head>
<body>
  <section class="card card-front">
    <div class="brand-name">Veltrane<br>Group</div>
    <div class="divider"></div>
    <div class="contact">
      <div class="contact-name">ROHESH KAMDAR</div>
      <div class="contact-title">CEO</div>
      <div class="contact-address">4180 Lindqvist Ave,<br>Tampa, FL 33482</div>
      <div class="contact-line">
        <svg viewBox="0 0 12 12" aria-hidden="true"><path d="M3 0h6a1 1 0 0 1 1 1v10a1 1 0 0 1-1 1H3a1 1 0 0 1-1-1V1a1 1 0 0 1 1-1zm0 1.5v8h6v-8z"/></svg>
        <span>604.781.2249</span>
      </div>
      <div class="contact-line">
        <svg viewBox="0 0 12 12" aria-hidden="true"><path d="M0 2h12v8H0zm1 1v.4l5 3.2 5-3.2V3zm0 1.6V9h10V4.6L6 7.8z"/></svg>
        <span>roheshkamdar@veltrane.com</span>
      </div>
      <div class="contact-line">
        <svg viewBox="0 0 12 12" aria-hidden="true"><circle cx="6" cy="6" r="6"/></svg>
        <span>www.veltrane.com</span>
      </div>
    </div>
  </section>

  <section class="card card-back">
    <div class="brand-mark">Veltrane<br>Group</div>
  </section>
</body>
</html>
```